Ledgerline Code Works business card design.

We are a software development company that develop Software for finance companies and related industries.

We need a 2 sided business card designed. We have a new logo already designed (see attached eps and ai) We are after a clean simple corporate look. One side with just our logo, and the second side with our details.

Greg Halvorsen
Managing Director

Suite 5 Level 8, 147 Marlow Street Sydney NSW 2000

Direct: +61 2 9387 4625
Mobile: +61 4 1736 8490
Email: gregh@lcw.net.au
Web: www.lcw.net.au

I have included 2 logo files an .ai and .eps. I noticed that the lines either side of the partners looks a bit jaggered and needs to be made sharper.

I would like to introduce a little colour somewhere rather than having it all black and white. But not over the top, keeping with a simple clean corporate look. Perhaps a light blue on some of the text?

If you have other ideas would be pleased to review

Regards

Greg H.

```html
<!DOCTYPE html>
<html lang="en">
<head>
<meta charset="utf-8">
<title>Ledgerline Code Works – Business Card</title>
<link rel="stylesheet" href="https://fonts.googleapis.com/css2?family=Open+Sans:wght@400;600;700;800&display=swap">
<style>
  :root {
    --stage: #3b3b3c;
    --ink: #1d1b1b;
    --paper: #f7f7f7;
    --sky: #5db3e3;
    --white: #ffffff;
  }
  * { box-sizing: border-box; margin: 0; padding: 0; }
  html, body { width: 1200px; height: 768px; overflow: hidden; }
  body {
    background: var(--stage);
    font-family: "Open Sans", Arial, sans-serif;
    position: relative;
  }
  .card {
    position: absolute;
    top: 234px;
    width: 520px;
    height: 300px;
    border-radius: 3px;
    overflow: hidden;
    box-shadow: 0 10px 24px rgba(0,0,0,.35);
  }
  .card--front { left: 50px; background: var(--ink); }
  .card--back { left: 630px; background: var(--paper); }

  .brand {
    position: absolute;
    display: flex;
    flex-direction: column;
    align-items: center;
  }
  .brand__mark {
    width: 22px; height: 22px;
    margin-bottom: 12px;
  }
  .brand__name {
    font-weight: 800;
    font-size: 22px;
    letter-spacing: .5px;
    text-transform: uppercase;
    white-space: nowrap;
  }
  .brand__rule {
    height: 1px;
    margin-top: 8px;
  }
  .card--front .brand { left: 0; right: 0; top: 108px; }
  .card--front .brand__mark { background: var(--white); }
  .card--front .brand__name { color: var(--white); }
  .card--front .brand__rule { background: rgba(255,255,255,.6); width: 340px; }

  .card--back .brand { left: 34px; top: 52px; }
  .card--back .brand__mark { background: var(--ink); }
  .card--back .brand__name { color: var(--ink); font-size: 19px; }
  .card--back .brand__rule { background: var(--ink); width: 290px; }

  .waves { position: absolute; inset: 0; width: 100%; height: 100%; }

  .person {
    position: absolute;
    right: 30px;
    top: 92px;
    text-align: right;
  }
  .person__name { color: var(--sky); font-weight: 700; font-size: 15px; }
  .person__role { color: var(--ink); font-size: 11px; margin-top: 2px; }

  .contact {
    position: absolute;
    right: 26px;
    bottom: 12px;
    list-style: none;
    text-align: right;
    color: var(--white);
    font-size: 11.5px;
    line-height: 15px;
  }
  .contact li { display: flex; justify-content: flex-end; align-items: center; gap: 8px; }
  .contact .icon { width: 11px; height: 11px; flex: none; }
  .contact .icon--blank { visibility: hidden; }
</style>
</head>
<body>

<section class="card card--front" aria-label="Card front">
  <div class="brand">
    <span class="brand__mark"></span>
    <span class="brand__name">Ledgerline Code Works</span>
    <span class="brand__rule"></span>
  </div>
</section>

<section class="card card--back" aria-label="Card back">
  <svg class="waves" viewBox="0 0 520 300" preserveAspectRatio="none" aria-hidden="true">
    <path d="M0,150 C40,195 140,225 260,212 C360,200 440,165 520,160 L520,300 L0,300 Z" fill="var(--ink)"/>
    <path d="M6,140 C60,182 160,205 270,196 C370,186 450,150 520,148" fill="none" stroke="var(--sky)" stroke-width="8"/>
    <path d="M0,128 C60,170 170,192 280,184 C380,176 455,140 520,138" fill="none" stroke="var(--sky)" stroke-width="2"/>
  </svg>

  <div class="brand">
    <span class="brand__mark"></span>
    <span class="brand__name">Ledgerline Code Works</span>
    <span class="brand__rule"></span>
  </div>

  <div class="person">
    <p class="person__name">Greg Halvorsen</p>
    <p class="person__role">Managing Director</p>
  </div>

  <ul class="contact">
    <li>+61 2 9387 4625
      <svg class="icon" viewBox="0 0 12 12"><path d="M2 1h3l1 3-1.5 1a6 6 0 0 0 2.5 2.5L8 6l3 1v3c-5 1-10-4-9-9z" fill="var(--sky)"/></svg>
    </li>
    <li>+61 4 1736 8490
      <svg class="icon" viewBox="0 0 12 12"><rect x="3" y="0.5" width="6" height="11" rx="1" fill="var(--sky)"/><rect x="4" y="2" width="4" height="7" fill="var(--ink)"/></svg>
    </li>
    <li>gregh@lcw.net.au
      <svg class="icon" viewBox="0 0 12 12"><rect x="0.5" y="2.5" width="11" height="7" fill="var(--sky)"/><path d="M0.5 2.5 6 7l5.5-4.5" fill="none" stroke="var(--ink)" stroke-width="1"/></svg>
    </li>
    <li>www.lcw.net.au
      <svg class="icon" viewBox="0 0 12 12"><circle cx="6" cy="6" r="5" fill="var(--sky)"/><path d="M1 6h10M6 1c-2.5 3-2.5 7 0 10M6 1c2.5 3 2.5 7 0 10" fill="none" stroke="var(--ink)" stroke-width=".8"/></svg>
    </li>
    <li>Suite 5 Level 8, 147
      <svg class="icon icon--blank" viewBox="0 0 12 12"></svg>
    </li>
    <li>Marlow Street | Sydney NSW 2000
      <svg class="icon" viewBox="0 0 12 12"><path d="M6 11.5C3 8 2.5 6.5 2.5 4.5a3.5 3.5 0 0 1 7 0C9.5 6.5 9 8 6 11.5z" fill="var(--sky)"/><circle cx="6" cy="4.5" r="1.3" fill="var(--ink)"/></svg>
    </li>
  </ul>
</section>

</body>
</html>
```